Modern book cover design

We are looking for a modern, powerful book cover for a general intrest book about how robots are going to take human jobs in the future.

The book title is "Gearstorm"

It also has a strap line "The end of human jobs and how robots will replace them"
Both the title and the strap line should be on the front cover

I have attached a number of book designs I like, and my author picture.
Updates

Reason: Some great submissions but none quite have that wow factor

Target Market(s)

This is a general intrest book, but the reader is likely to be male 30-50

Requirements
Must have
• -Title "Gearstorm"

-Strap-line "The end of human jobs and how robots will replace them"

-Be compliant with PressNook Cover Design Criteria(www.pressnook-example.com)

-Book size : 5.5 x 8.5 inches

-Spine size : 0.625 inches

-Must have one author picture on the back cover(attached)

-Must have the following author description on back cover:
"Tom Hale is a leading futurologist, technologist, inventor, and entrepreneur. With over twenty years of experience in technology and innovation, Tom has travelled the world seeking out and developing new technologies. As a leading voice on the challenges and benefits of tomorrow’s technology, he has advised some of the world’s leading institutions, including the Amber Hall, regarding technological preparations for the future. He is the recipient of the millennium entrepreneur of the year award and has appeared on numerous technology and philanthropy television programs, as well as presenting Steel Dawn Weekly on Robotics."

-Must have the following book description on back cover:
“Gearstorm is a look at the rapidly changing face of robotics and how it will revolutionize employment over the next thirty years. Tom Hale lays out the arguments in favor of and against the mechanization of our society, as well as the advantages and untold risks as we march into this ever-present future.”

-Must have the following quote on the back cover:
"A fascinating look into the future of robotics and their impact on humanity, be prepared to question when robots will replace you - Derek Lansford, Professor of Cybernetics at the University of Elmsworth”

-Example barcode

```html
<!DOCTYPE html>
<html lang="en">
<head>
<meta charset="utf-8">
<title>Gearstorm – Book Cover</title>
<link rel="stylesheet" href="https://fonts.googleapis.com/css2?family=Anton&family=Black+Ops+One&family=Cinzel:wght@400;700&family=Marcellus&family=Tinos:ital,wght@0,400;1,400;1,700&display=swap">
<style>
  :root {
    --page: #ffffff;
    --cover: #000000;
    --ink: #ffffff;
    --title-top: #ffe800;
    --title-bottom: #ff9d00;
    --photo: #8c8c8c;
    --glow: #5fb0ff;
  }
  * { margin: 0; padding: 0; box-sizing: border-box; }
  html, body { width: 1200px; height: 1000px; overflow: hidden; background: var(--page); }
  .canvas { position: relative; width: 1200px; height: 1000px; background: var(--page); }
  .cover { position: absolute; left: 88px; top: 121px; width: 1041px; height: 768px; background: var(--cover); color: var(--ink); }

  /* Back cover */
  .back { position: absolute; left: 0; top: 0; width: 497px; height: 768px; }
  .back-heading { position: absolute; left: 0; width: 497px; text-align: center; font-family: "Black Ops One", sans-serif; font-size: 18px; letter-spacing: 3px; }
  .back-heading--book { top: 68px; }
  .back-heading--author { top: 296px; }
  .book-blurb { position: absolute; left: 22px; top: 114px; width: 450px; text-align: center; font-family: "Tinos", serif; font-size: 15.5px; line-height: 1.3; }
  .book-quote { position: absolute; left: 22px; top: 228px; width: 450px; font-family: "Tinos", serif; font-style: italic; font-size: 15.5px; line-height: 1.3; text-align: justify; }
  .book-quote cite { font-weight: 700; font-size: 14.5px; }
  .author-photo { position: absolute; left: 28px; top: 330px; width: 109px; height: 157px; background: linear-gradient(180deg, #bdbdbd, var(--photo) 60%, #4a4a4a); }
  .author-name-back { position: absolute; left: 144px; top: 426px; font-family: "Cinzel", serif; font-size: 62px; line-height: 1; letter-spacing: 1px; }
  .author-bio { position: absolute; left: 12px; top: 489px; width: 446px; font-family: "Tinos", serif; font-size: 15.5px; line-height: 1.3; text-align: justify; }

  /* Spine */
  .spine { position: absolute; left: 497px; top: 0; width: 45px; height: 768px; }
  .spine-text { position: absolute; writing-mode: vertical-rl; white-space: nowrap; }
  .spine-title { left: 6px; top: 18px; font-family: "Anton", sans-serif; font-size: 28px; letter-spacing: 2px; color: var(--title-bottom); }
  .spine-author { left: 4px; top: 236px; font-family: "Black Ops One", sans-serif; font-size: 30px; letter-spacing: 14px; }
  .spine-strap { left: 12px; top: 494px; font-family: "Marcellus", serif; font-size: 13.5px; line-height: 1.1; text-align: center; }

  /* Front cover */
  .front { position: absolute; left: 542px; top: 0; width: 499px; height: 768px; overflow: hidden; }
  .front-art { position: absolute; left: 0; top: 330px; width: 499px; height: 438px;
    background:
      radial-gradient(ellipse 60% 4% at 55% 57px, rgba(200,230,255,0.95), rgba(80,160,255,0.4) 40%, transparent 75%),
      radial-gradient(ellipse 30% 22% at 55% 60px, rgba(60,140,255,0.45), transparent 70%),
      radial-gradient(ellipse 32% 60% at 55% 70%, #3b3b3e, #1a1a1c 60%, transparent 90%);
  }
  .front-title { position: absolute; left: 20px; top: 28px; width: 460px; height: 150px; }
  .strap { position: absolute; left: 0; top: 198px; width: 499px; text-align: center; font-family: "Marcellus", serif; font-size: 24px; line-height: 1.15; }
  .strap-rule { position: absolute; left: 173px; width: 175px; height: 3px; background: var(--ink); }
  .strap-rule--top { top: 198px; }
  .strap-rule--bottom { top: 270px; }
  .strap-text { position: absolute; left: 0; top: 210px; width: 499px; }
  .author-name-front { position: absolute; left: 0; top: 660px; width: 535px; text-align: center; font-family: "Cinzel", serif; font-size: 70px; line-height: 1; }
</style>
</head>
<body>
<div class="canvas">
  <div class="cover">
    <section class="back">
      <h2 class="back-heading back-heading--book">About the Book</h2>
      <p class="book-blurb">Gearstorm is a look at the rapidly changing face of robotics and how it will revolutionize employment over the next thirty years.<br>Tom Hale lays out the arguments in favor of and against the mechanization of our society, as well as the advantages and untold risks as we march into this ever-present future</p>
      <p class="book-quote">A fascinating look into the future of robotics and their impact on humanity, be prepared to question when robots will replace you -<br><cite>Derek Lansford, Professor of Cybernetics at the University of Elmsworth</cite></p>
      <h2 class="back-heading back-heading--author">About the Author</h2>
      <div class="author-photo" role="img" aria-label="Black and white portrait photograph of the author"></div>
      <div class="author-name-back">TOM HALE</div>
      <p class="author-bio">&nbsp;is a leading futurologist, technologist, inventor, and entrepreneur. With over twenty years of experience in technology and innovation, Tom has travelled the world seeking out and developing new technologies. As a leading voice on the challenges and benefits of tomorrow’s technology, he has advised some of the world’s leading institutions, including the Amber Hall, regarding technological preparations for the future. He is the recipient of the millennium entrepreneur of the year award and has appeared on numerous technology and philanthropy television programs, as well as presenting Steel Dawn Weekly on Robotics.</p>
    </section>

    <section class="spine">
      <div class="spine-text spine-title">GEARSTORM</div>
      <div class="spine-text spine-author">TOM HALE</div>
      <div class="spine-text spine-strap">THE END OF HUMAN JOBS AND HOW<br>ROBOTS WILL REPLACE THEM</div>
    </section>

    <section class="front">
      <div class="front-art" role="img" aria-label="Dark illustration of a robotic figure with blue eyes beneath a bright blue light flare"></div>
      <svg class="front-title" viewBox="0 0 460 150" aria-label="Gearstorm">
        <defs>
          <linearGradient id="titleFill" x1="0" y1="0" x2="1" y2="0">
            <stop offset="0" stop-color="var(--title-top)"/>
            <stop offset="1" stop-color="var(--title-bottom)"/>
          </linearGradient>
        </defs>
        <text x="0" y="145" textLength="460" lengthAdjust="spacingAndGlyphs" font-family="Anton, sans-serif" font-size="190" fill="url(#titleFill)">GEARSTORM</text>
      </svg>
      <div class="strap-rule strap-rule--top"></div>
      <div class="strap"><div class="strap-text">THE END OF HUMAN JOBS AND HOW<br>ROBOTS WILL REPLACE THEM</div></div>
      <div class="strap-rule strap-rule--bottom"></div>
      <div class="author-name-front">TOM HALE</div>
    </section>
  </div>
</div>
</body>
</html>
```